Web Design for guards MMJ transport and security services

Harbor Crest Protective solutions a tallow unified company, is looking for a designer to create a website that displays our service portfolio. We need marketing pictures and content to be created in a original and competitive fashion, intriguing to our customers. We will need forms on the website to be created for calendar booking (somehow integrate into exchange if possible) and general inquiry forms. There will need to be pages dedicated to our staff, MMJ trasnport & Courier services, our vehicles, alarm systems, video systems, video monitoring, private investigations, and surveillance aduit and compliance investigations, payment gateway integration, and general company information. I Have attached our main company logo. Also have a emphasis on being state licensed by the Colorado RPB. Have a link to our parent site, tallowcctv.example

Target Market(s)

Colorado Marijuana industry, MMJ transport services, guard services, armed gaurd services.

Contact Information for Business Card

Would like a sleek simple design highlighting what we offer. must match the website and have a overall professional straight to the point appearance.

Number of Pages Required

1 page

Colors
33b8a4
00a990
9bcb3c
acd036
cadf82
85cae6
33a6d7
0792cd

Requirements
Must have
• Easy to use, lots of images, professional.
Nice to have
• Creativity

```html
<!DOCTYPE html>
<html lang="en">
<head>
<meta charset="utf-8">
<title>Harbor Crest Protective Solutions</title>
<link rel="stylesheet" href="https://fonts.googleapis.com/css2?family=Open+Sans:wght@400;600;700&display=swap">
<style>
:root{
  --blue:#0a8dcd;
  --navy-deep:#0c1d2b;
  --green:#9bcb3c;
  --ink:#1d1d1d;
  --gray:#6f6f6f;
  --gray-light:#9a9a9a;
  --white:#ffffff;
}
*{box-sizing:border-box;margin:0;padding:0}
html,body{width:1200px;height:2287px;overflow:hidden}
body{position:relative;font-family:"Open Sans",Arial,sans-serif;color:var(--ink);background:var(--white)}
.abs{position:absolute}
svg{display:block}

/* hero */
.hero{left:0;top:0;width:1200px;height:602px;background:linear-gradient(115deg,#1c3550 0%,#33587c 35%,#587a98 55%,#2c4a68 80%,#1a324c 100%)}
.brand{left:111px;top:40px;display:flex;align-items:center;gap:10px;color:var(--white);font-weight:700;font-size:22px}
.brand-dot{width:26px;height:26px;border-radius:50%;background:#c8202f}
.topbar{right:111px;top:40px;display:flex;gap:24px;color:var(--white);font-size:11.5px;font-weight:600;letter-spacing:.3px}
.topbar span{display:flex;align-items:center;gap:8px}
.nav{left:111px;top:96px;width:978px;height:36px;border-bottom:1px solid rgba(255,255,255,.85)}
.nav ul{list-style:none;height:100%}
.nav li{color:var(--white);font-size:12px;font-weight:700;position:absolute;top:3px}
.nav li.active::after{content:"";position:absolute;left:-9px;right:-9px;top:30px;height:4px;background:var(--blue)}
.dropdown{left:727px;top:131px;width:290px;height:319px;background:var(--blue);padding:12px 27px}
.dropdown li{list-style:none;color:var(--white);font-size:11.5px;font-weight:600;height:41px;line-height:41px;border-bottom:1px solid rgba(255,255,255,.25)}
.dropdown li:last-child{border-bottom:none}
.hero-title{left:108px;top:304px;color:var(--white);font-size:52px;font-weight:600;letter-spacing:.5px}
.hero-text{left:111px;top:372px;width:460px;color:var(--white);font-size:12px;line-height:26px}
.hero-arrows{left:111px;top:438px;display:flex;gap:10px}

/* features */
.features{left:0;top:602px;width:1200px;height:225px;background:var(--blue)}
.feature-arch{top:514px;width:176px;height:88px;overflow:hidden}
.feature-arch::before{content:"";position:absolute;left:0;top:0;width:176px;height:176px;border-radius:50%;background:var(--blue);box-shadow:inset 0 0 0 4px rgba(255,255,255,.22)}
.feature-icon{top:552px;width:176px;display:flex;justify-content:center}
.feature{top:640px;width:280px;text-align:center;color:var(--white)}
.feature h3{font-size:20px;font-weight:700;letter-spacing:.5px}
.feature hr{width:90px;margin:12px auto 16px;border:none;border-top:1px solid rgba(255,255,255,.4)}
.feature p{font-size:12px;line-height:26px;text-align:justify;text-align-last:center}

/* welcome */
.welcome-mark{left:570px;top:864px;width:60px;height:60px;border-radius:50%;background:var(--green)}
.welcome-title{left:0;top:938px;width:1200px;text-align:center;font-size:26px;font-weight:700}
.welcome-title em{font-style:normal;color:var(--blue)}
.welcome-text{left:111px;top:986px;width:978px;text-align:center;color:var(--gray);font-size:12px;line-height:31px}

/* services */
.services-head{left:0;top:1118px;width:1200px;height:76px;background:var(--blue);color:var(--white);font-size:25px;font-weight:700;text-align:center;line-height:76px}
.services-body{left:0;top:1194px;width:1200px;height:481px;background:linear-gradient(120deg,#183a55 0%,#12304a 50%,#0e2a42 100%)}
.tabs{left:111px;top:1194px;width:978px;height:67px;background:rgba(0,0,0,.25);color:var(--white);font-size:15px;font-weight:700}
.tab{position:absolute;top:22px}
.tab.active::after{content:"";position:absolute;left:0;right:0;top:27px;height:3px;background:var(--green)}
.card{top:1305px;width:226px;height:324px;background:var(--white)}
.card-photo{height:144px}
.card h4{margin:23px 21px 0;font-size:13.5px;font-weight:600;color:var(--ink)}
.card p{margin:12px 21px 0;font-size:11px;line-height:26px;color:var(--gray)}
.read-more{position:absolute;left:21px;top:282px;font-size:11.5px;font-weight:700;color:var(--blue);display:flex;align-items:center;gap:4px}

/* news & partners */
.section-title{top:1732px;font-size:26px;font-weight:700}
.section-title em{font-style:normal;color:var(--blue)}
.news-photo{left:111px;top:1792px;width:212px;height:142px;border:2px solid #e8e8e8;background:linear-gradient(135deg,#d9dcdf,#aeb5bb)}
.news-date{left:113px;top:1892px;width:208px;height:40px;background:var(--blue);color:var(--white);font-size:12px;font-weight:600;text-align:center;line-height:40px}
.news-lead{left:349px;top:1784px;width:312px;font-size:13px;line-height:30px;color:var(--ink)}
.news-body{left:349px;top:1852px;width:312px;font-size:12px;line-height:29px;color:var(--gray-light);text-align:justify}
.partners-text{left:697px;top:1784px;width:392px;font-size:12.5px;line-height:30px;color:var(--ink)}
.partner-name{left:705px;top:1876px;display:flex;align-items:center;gap:8px;color:var(--blue);font-size:19px;font-weight:700}
.partner-name i{width:32px;height:32px;border-radius:50%;background:var(--blue);display:block}
.partner-badge{left:924px;top:1858px;width:67px;height:67px;border-radius:50%;background:#d9a520;border:5px solid #1b1b1b}

/* footer */
.footer{left:0;top:1995px;width:1200px;height:207px;background:var(--blue);color:var(--white)}
.footer h5{position:absolute;top:30px;font-size:15px;font-weight:700}
.footer-rule{position:absolute;top:30px;width:1px;height:150px;background:rgba(255,255,255,.3)}
.contact-list{position:absolute;left:111px;top:62px;font-size:11.5px;line-height:19px}
.contact-list div{display:flex;gap:10px;margin-bottom:9px}
.links{position:absolute;left:386px;top:62px;list-style:none;font-size:12px;line-height:26px}
.quote{position:absolute;left:576px;top:62px;width:513px;font-size:12px;line-height:26px}
.avatar{position:absolute;left:578px;top:2117px;width:50px;height:50px;border-radius:50%;background:#b9a688;border:2px solid var(--white)}
.cite{position:absolute;left:640px;top:2119px;font-size:15px;color:var(--white)}
.cite small{display:block;font-size:12px;opacity:.9}

.base{left:0;top:2202px;width:1200px;height:85px;background:var(--navy-deep);color:var(--white)}
.copyright{position:absolute;left:111px;top:33px;font-size:11.5px}
.copyright a{color:var(--green);text-decoration:none;margin-left:10px}
.social{position:absolute;left:971px;top:30px;display:flex;gap:15px}
.social span{width:22px;height:22px;display:block;border-radius:2px}
</style>
</head>
<body>

<!-- hero -->
<div class="abs hero" role="img" aria-label="Photo of a glass and steel building interior in blue tones"></div>
<div class="abs brand"><span class="brand-dot"></span>Harbor Crest</div>
<div class="abs topbar">
  <span><svg width="12" height="16" viewBox="0 0 12 16"><rect x="1" y="1" width="10" height="14" rx="2" fill="none" stroke="#9bcb3c" stroke-width="1.6"/><circle cx="6" cy="12.5" r="1" fill="#9bcb3c"/></svg>CALL US : 123 456 7890</span>
  <span><svg width="18" height="14" viewBox="0 0 18 14"><rect x="1" y="1" width="16" height="12" rx="1" fill="none" stroke="#9bcb3c" stroke-width="1.6"/><path d="M1 2l8 6 8-6" fill="none" stroke="#9bcb3c" stroke-width="1.6"/></svg>EMAIL US : INFO@HARBORCREST.EXAMPLE</span>
</div>
<nav class="abs nav">
  <ul>
    <li class="active" style="left:290px">HOME</li>
    <li style="left:385px">ABOUT US</li>
    <li style="left:505px">OUR STAFF</li>
    <li style="left:630px">SERVICES &#8964;</li>
    <li style="left:757px">OUR VEHICLES</li>
    <li style="left:901px">CONTACT US</li>
  </ul>
</nav>
<ul class="abs dropdown">
  <li>MMJ TRANSPORT &amp; COURIER SERVICES</li>
  <li>ALARM SYSTEMS</li>
  <li>VIDEO SYSTEMS</li>
  <li>VIDEO MONITORING</li>
  <li>PRIVATE INVESTIGATIONS</li>
  <li>SURVEILLANCE AUDIT</li>
  <li>COMPLIANCE INVESTIGATIONS</li>
</ul>
<h1 class="abs hero-title">SAFE &amp; SECURE</h1>
<p class="abs hero-text">Lorem ipsum dolor sit amet, consectetur adipiscing elit. Morbi vel aliquet eros. Sed sodales, libero in molestie convallis, sapien lorem scelerisque enim.</p>
<div class="abs hero-arrows">
  <svg width="14" height="22" viewBox="0 0 14 22"><path d="M11 3L3 11l8 8" fill="none" stroke="#fff" stroke-width="3.5"/></svg>
  <svg width="14" height="22" viewBox="0 0 14 22"><path d="M3 3l8 8-8 8" fill="none" stroke="#fff" stroke-width="3.5"/></svg>
</div>

<!-- features -->
<div class="abs features"></div>
<div class="abs feature-arch" style="left:179px"></div>
<div class="abs feature-arch" style="left:511px"></div>
<div class="abs feature-arch" style="left:845px"></div>
<div class="abs feature-icon" style="left:179px">
  <svg width="80" height="56" viewBox="0 0 80 56" fill="none" stroke="#fff" stroke-width="3"><path d="M22 8h30v30H22z"/><path d="M52 18h12l10 12v8H52"/><circle cx="32" cy="42" r="6"/><circle cx="64" cy="42" r="6"/><path d="M2 16h14M6 24h10M2 32h14"/></svg>
</div>
<div class="abs feature-icon" style="left:511px;top:546px">
  <svg width="56" height="64" viewBox="0 0 56 64" fill="none" stroke="#fff" stroke-width="3"><path d="M28 3l22 8v18c0 15-10 27-22 32C16 56 6 44 6 29V11z"/><path d="M18 32l7 7 14-15"/></svg>
</div>
<div class="abs feature-icon" style="left:845px">
  <svg width="66" height="56" viewBox="0 0 66 56" fill="none" stroke="#fff" stroke-width="3"><circle cx="24" cy="16" r="11"/><path d="M3 52c0-13 9-21 21-21s21 8 21 21z"/><circle cx="46" cy="20" r="8"/><path d="M44 33c11 0 19 6 19 19H48"/></svg>
</div>
<div class="abs feature" style="left:127px"><h3>TRANSPORT</h3><hr><p>Fusce finibus ante risus, in efficitur lacus semper ac. Sed leo urna, facilisis vitae imperdiet et, rutrum et turpis.</p></div>
<div class="abs feature" style="left:459px"><h3>SECURITY</h3><hr><p>Duis vel mattis ex. Duis eget quam in mi tincidunt posuere. Etiam nulla lorem, condimentum vitae massa vel, venenatis gravida nunc.</p></div>
<div class="abs feature" style="left:793px"><h3>OUR STAFFS</h3><hr><p>Lorem ipsum dolor sit amet, consectetur adipiscing elit. Morbi vel aliquet eros. Sed sodales, libero in molestie convallis.</p></div>

<!-- welcome -->
<div class="abs welcome-mark"></div>
<h2 class="abs welcome-title">WELCOME TO <em>HARBOR CREST PROTECTIVE SOLUTIONS</em></h2>
<p class="abs welcome-text">Morbi lobortis nisi a ultrices rhoncus. Nunc efficitur turpis mi, a aliquam mi facilisis et. Fusce nulla tortor, consectetur vitae suscipit non, hendrerit non arcu. Sed vitae feugiat velit. Morbi id venenatis nisi. Mauris feugiat malesuada tempus. Curabitur hendrerit egestas velit vitae convallis. In ut tincidunt purus. Pellentesque non orci nisi. Vestibulum quis enim convallis, dapibus massa in, suscipit quam. Aliquam vitae fermentum lorem.</p>

<!-- services -->
<h2 class="abs services-head">OUR SERVICES</h2>
<div class="abs services-body"></div>
<div class="abs tabs">
  <span class="tab active" style="left:86px">SECURITY SERVICES</span>
  <span class="tab" style="left:334px">TRANSPORT SERVICES</span>
</div>

<div class="abs card" style="left:111px">
  <div class="card-photo" role="img" aria-label="Photo of a red alarm bell on a white wall" style="background:linear-gradient(135deg,#d8d8d8,#9a9a9a 55%,#b8262c 60%,#c9c9c9)"></div>
  <h4>ALARM SYSTEMS</h4>
  <p>Lorem ipsum dolor sit amet, con sectetur adipiscing elit. Morbi v zel aliquet eros.</p>
  <span class="read-more"><svg width="10" height="10" viewBox="0 0 10 10"><path d="M5 1l4 4-4 4-4-4z" fill="none" stroke="#0a8dcd" stroke-width="1.5"/></svg>READ MORE</span>
</div>
<div class="abs card" style="left:361px">
  <div class="card-photo" role="img" aria-label="Photo of a dome security camera on a concrete ceiling" style="background:linear-gradient(135deg,#cfcfcf,#a9a9a9)"></div>
  <h4>VIDEO SYSTEMS</h4>
  <p>Morbi id venenatis nisi. Mauris fe ugiat malesuada tempus. Cur abitur hendrerit egestas.</p>
  <span class="read-more"><svg width="10" height="10" viewBox="0 0 10 10"><path d="M5 1l4 4-4 4-4-4z" fill="none" stroke="#0a8dcd" stroke-width="1.5"/></svg>READ MORE</span>
</div>
<div class="abs card" style="left:613px">
  <div class="card-photo" role="img" aria-label="Photo of an investigator examining a document with a magnifying glass" style="background:linear-gradient(135deg,#6fa6d4,#b9d4ea 60%,#e6e6e6)"></div>
  <h4>PRIVATE INVESTIGATIONS</h4>
  <p>Lorem ipsum dolor sit amet, con sectetur adipiscing elit. Morbi v zel aliquet eros.</p>
  <span class="read-more"><svg width="10" height="10" viewBox="0 0 10 10"><path d="M5 1l4 4-4 4-4-4z" fill="none" stroke="#0a8dcd" stroke-width="1.5"/></svg>READ MORE</span>
</div>
<div class="abs card" style="left:863px">
  <div class="card-photo" role="img" aria-label="Photo of a hand touching a digital audit display" style="background:linear-gradient(135deg,#8a8a8a,#4e4e4e)"></div>
  <h4>SURVEILLANCE AUDIT</h4>
  <p>Morbi id venenatis nisi. Mauris fe ugiat malesuada tempus. Cur abitur hendrerit egestas.</p>
  <span class="read-more"><svg width="10" height="10" viewBox="0 0 10 10"><path d="M5 1l4 4-4 4-4-4z" fill="none" stroke="#0a8dcd" stroke-width="1.5"/></svg>READ MORE</span>
</div>

<!-- latest news -->
<h2 class="abs section-title" style="left:110px">LATEST <em>NEWS</em></h2>
<svg class="abs" style="left:620px;top:1740px" width="42" height="20" viewBox="0 0 42 20"><path d="M9 3L3 10l6 7M33 3l6 7-6 7" fill="none" stroke="#333" stroke-width="3"/></svg>
<div class="abs news-photo" role="img" aria-label="Photo of a hand entering a code on an alarm keypad"></div>
<div class="abs news-date">MAR 10 ,2016</div>
<p class="abs news-lead">Lorem ipsum dolor sit amet, consectetur adipiscing elit. Morbi vel aliquet eros.</p>
<p class="abs news-body">Aliquam imperdiet erat sit amet ipsum elementum viverra. Sed finibus commodo nibh accumsan vehicula. Morbi vitae lobortis magna.</p>

<!-- partners -->
<h2 class="abs section-title" style="left:697px">WE <em>WORK WITH</em></h2>
<p class="abs partners-text">Duis eget quam in mi tincidunt posuere. Etiam nulla lorem, con dimentum vitae massa vel, venenatis gravida nunc.</p>
<div class="abs partner-name"><i></i>tallow unified</div>
<div class="abs partner-badge" aria-label="RPB state license badge"></div>

<!-- footer -->
<footer class="abs footer">
  <h5 style="left:110px">CONTACT US</h5>
  <div class="footer-rule" style="left:338px"></div>
  <h5 style="left:384px">QUICK LINKS</h5>
  <div class="footer-rule" style="left:534px"></div>
  <h5 style="left:576px">TESTIMONIALS</h5>
  <svg style="position:absolute;left:1056px;top:34px" width="32" height="16" viewBox="0 0 32 16"><path d="M7 2L2 8l5 6M25 2l5 6-5 6" fill="none" stroke="#fff" stroke-width="2.5"/></svg>
  <div class="contact-list">
    <div><svg width="12" height="16" viewBox="0 0 12 16"><path d="M6 15S1 9 1 6a5 5 0 0110 0c0 3-5 9-5 9z" fill="#9bcb3c"/><circle cx="6" cy="6" r="2" fill="#0a8dcd"/></svg><span>HARBOR CREST<br>118 Lorem Ipsm, Lorem Ipsm<br>Lorem Ipsm 80412</span></div>
    <div><svg width="14" height="12" viewBox="0 0 14 12"><rect width="14" height="12" rx="1" fill="#9bcb3c"/><path d="M1 2l6 5 6-5" fill="none" stroke="#0a8dcd" stroke-width="1.4"/></svg><span>info@harborcrest.example</span></div>
    <div><svg width="14" height="14" viewBox="0 0 14 14"><rect width="14" height="14" rx="2" fill="#9bcb3c"/><path d="M4 3l2 2-1 2 2 2 2-1 2 2-2 1c-3 0-6-3-6-6z" fill="#0a8dcd"/></svg><span>888-555-0142</span></div>
  </div>
  <ul class="links">
    <li>About us</li><li>Services</li><li>Our vehicles</li><li>Blog</li><li>Contact Us</li>
  </ul>
  <p class="quote">Nullam auctor neque nec tortor sagittis congue. Aliquam est metus, ornare a dictum id, finibus eget urna. Sed laoreet lacus vitae sapien bibendum sodales.</p>
</footer>
<div class="avatar" role="img" aria-label="Portrait of the client giving the testimonial"></div>
<div class="cite">- Nora Vale<small>Location</small></div>

<div class="abs base">
  <p class="copyright">Copyright © 2016 Harbor Crest Protective solutions. All Rights Reserved. <a>Privacy Policy</a><a>Terms of Service</a></p>
  <div class="social" aria-label="Social links">
    <span style="background:#3b5998"></span>
    <span style="background:#1da1f2"></span>
    <span style="background:#dd4b39"></span>
    <span style="background:#f39c12"></span>
  </div>
</div>

</body>
</html>
```